Brindle Sky Port needs a new upscale business card design for our high end aircraft hangar complex

Brindle Sky Port (BSP) is a large, upscale jet hangar complex in the US housing expensive aircraft. We need a new business card design, using our current logo. We will be attending a industry convention and need a card design that will stand out and be remembered by aircraft owners and private pilots.

Target Market(s)

Aircraft pilots or owners looking for a new upscale hangar

Industry/Entity Type

Airport

Contact Information for Business Card

I like to use very heavy card stock, 400#, double sided. Square, no rounded edges please.

Colors
3276b5
0255a3
85abd2

Requirements
Must have
• An expensive, classy design, vivid colors.
Nice to have
• Needs to look very expensive and classy, and have some "pop". Designer must be able to download or copy my current typeface or fonts.
• One card side might be black with the "Logo and Brindle Sky Port Double line image in blue (or try gold, or glossy black), and perhaps have a grayed out "K720 jet silhouette". The other card side would have our contact info, and perhaps the "BSP Logo only". I'd like my contact info 'stacked', not in a paragraph format.
Should not have
• Should not look "too busy". Having a double-sided card will help.

```html
<!DOCTYPE html>
<html lang="en">
<head>
<meta charset="utf-8">
<title>Brindle Sky Port – Business Card</title>
<link rel="stylesheet" href="https://fonts.googleapis.com/css2?family=Open+Sans:wght@400;600;700&display=swap">
<style>
  :root {
    --backdrop: #9c9d9d;
    --card: #0f0f10;
    --card-edge: #161617;
    --blue: #3276b5;
    --blue-deep: #0255a3;
    --blue-light: #85abd2;
    --text: #d9d9d9;
    --rule: #6b6b6b;
    --silver: #b9b9bb;
  }
  * { box-sizing: border-box; margin: 0; padding: 0; }
  html, body { width: 1105px; height: 1200px; overflow: hidden; }
  body {
    background: var(--backdrop);
    font-family: "Open Sans", Arial, sans-serif;
    position: relative;
  }
  .card {
    position: absolute;
    left: 182px;
    width: 746px;
    height: 427px;
    background: linear-gradient(90deg, var(--card), var(--card-edge) 50%, var(--card));
    overflow: hidden;
  }
  .card--front { top: 119px; }
  .card--back { top: 637px; }

  .brand-mark {
    position: absolute;
    display: flex;
    align-items: center;
    gap: 14px;
    color: var(--blue);
    font-weight: 700;
    line-height: 1;
  }
  .brand-mark__square {
    background: var(--blue);
    flex: none;
  }
  .card--front .brand-mark { left: 84px; top: 168px; font-size: 78px; letter-spacing: 4px; }
  .card--front .brand-mark__square { width: 26px; height: 26px; }

  .divider {
    position: absolute;
    left: 377px; top: 75px;
    width: 1px; height: 248px;
    background: linear-gradient(180deg, transparent, var(--rule) 20%, var(--rule) 80%, transparent);
  }
  .contact {
    position: absolute;
    left: 423px; top: 70px;
    color: var(--text);
  }
  .contact__name {
    color: var(--blue);
    font-size: 27px;
    font-weight: 600;
    letter-spacing: 0.5px;
    line-height: 1.2;
  }
  .contact__title { font-size: 19px; margin-top: 2px; }
  .contact__address { font-size: 19px; line-height: 27px; margin-top: 13px; }
  .contact__lines { list-style: none; margin-top: 12px; font-size: 19px; line-height: 29px; }
  .contact__label { color: var(--blue); display: inline-block; width: 22px; }

  .footer-band {
    position: absolute;
    left: 0; bottom: 0;
    width: 420px; height: 18px;
    background: var(--silver);
  }
  .footer-tab {
    position: absolute;
    right: 0; bottom: 0;
    width: 350px; height: 42px;
    background: var(--blue);
    border-top-left-radius: 40px 42px;
    color: #0d1d33;
    font-size: 19px;
    letter-spacing: 3px;
    display: flex; align-items: center; justify-content: center;
    padding-left: 20px;
  }

  .jet-photo {
    position: absolute;
    right: 0; top: 0;
    width: 400px; height: 427px;
    background: radial-gradient(ellipse 60% 45% at 62% 68%, #262628, #151516 70%, transparent);
  }
  .card--back .brand-mark {
    left: 76px; top: 96px;
    flex-direction: column;
    align-items: flex-start;
    gap: 10px;
  }
  .brand-mark__row { display: flex; align-items: center; gap: 16px; font-size: 112px; letter-spacing: 6px; }
  .card--back .brand-mark__square { width: 34px; height: 34px; }
  .brand-mark__name { font-size: 34px; letter-spacing: 1px; padding-left: 4px; }
</style>
</head>
<body>
  <section class="card card--front" aria-label="Card front">
    <div class="brand-mark"><span class="brand-mark__square"></span>BSP</div>
    <div class="divider"></div>
    <div class="contact">
      <p class="contact__name">MARLA QUENBY</p>
      <p class="contact__title">CEO/ Founder</p>
      <p class="contact__address">4120 Heron Field Road<br>Kestrel Bay, Alaska 99587</p>
      <ul class="contact__lines">
        <li><span class="contact__label">P</span>(555) 014-2273</li>
        <li><span class="contact__label">C</span>(555) 019-4461</li>
        <li><span class="contact__label">F</span>(555) 017-3308</li>
        <li><span class="contact__label">E</span>hello@bskyport.com</li>
      </ul>
    </div>
    <div class="footer-band"></div>
    <div class="footer-tab">www.bskyport.com</div>
  </section>

  <section class="card card--back" aria-label="Card back">
    <div class="jet-photo" role="img" aria-label="Faint grey silhouette of a K720 private jet, nose-on"></div>
    <div class="brand-mark">
      <div class="brand-mark__row"><span class="brand-mark__square"></span>BSP</div>
      <div class="brand-mark__name">Brindle Sky Port</div>
    </div>
  </section>
</body>
</html>
```